Interior designer needs a power point template design

I need a template PowerPoint design for my client presentations. The presentations I prepare for my clients usually include the furniture project, the detail of the selected furniture, and the costs. There are a lot of images I insert. What I need is to have a template that I can use for all my presentations, where from time to time I will insert the specific images and descriptions I want to insert. What will always be the same will be the cover, the colors, the font, and the design of the internal sections.
I already have my logo that I would like to insert on each page of the presentation (in small size).
In summary, I need:
- basic template design
- cover with an image chosen by Pictavale photo
- design an internal section/chapter
- internal page design.

I like the clolors of pink and brown <8please see image attached)
Images (will come from Pictavale photo)
● entrance/hall
● living room
● dining room
● Bathroom
● Closet
● Kids room
● Master bedroom
● Master bathroom
● Kitchen
● Office
● Laundry
● Balcony or Terrace

Target Market(s)

Customers (both residential and commercial projects)

Industry/Entity Type

interior design

Font styles to use
Other font styles liked:
• I like courier new

Requirements
Must have
• beautiful design
Should not have
• animations

```html
<!DOCTYPE html>
<html lang="en">
<head>
<meta charset="utf-8">
<title>Casa Orlena – Presentation Template</title>
<link href="https://fonts.googleapis.com/css2?family=Oswald:wght@300;400&family=Montserrat:wght@400;500&display=swap" rel="stylesheet">
<style>
:root{
  --pink:#f4677f;
  --pink-line:#ee5f78;
  --cream:#f7f5f0;
  --white:#ffffff;
  --brown:#6b2a14;
  --body:#4a3a34;
  --terracotta:#b8766a;
  --terracotta-dark:#a96759;
}
*{margin:0;padding:0;box-sizing:border-box}
html,body{width:1200px;height:3429px;overflow:hidden;background:var(--pink)}
body{position:relative;font-family:"Montserrat",sans-serif;color:var(--body)}
.slide{position:absolute;left:24px;width:1152px;height:648px;background:var(--cream);overflow:hidden}
.slide--cover{top:24px;height:645px}
.slide--bedroom{top:696px}
.slide--closet{top:1369px}
.slide--bathroom{top:2042px}
.slide--thanks{top:2717px}
.abs{position:absolute}
.heading{font-family:"Oswald",sans-serif;font-weight:400;color:var(--brown);letter-spacing:-.5px;line-height:1;text-transform:uppercase;display:flex;align-items:center}
.heading::after{content:"";display:inline-block;width:60px;height:2px;background:currentColor;margin-left:14px}
.heading--plain::after{display:none}
.body-text{font-size:12.5px;line-height:22.5px;color:var(--body)}
.subheading{font-size:20px;color:var(--brown);font-weight:400}
.visual{position:absolute}
.frame{position:absolute;border:2px solid var(--pink-line)}
.block{position:absolute;background:var(--pink)}

/* cover */
.brand{left:70px;top:50px;width:140px;text-align:center}
.brand__mark{width:92px;height:92px;border:2px solid var(--brown);border-radius:50%;margin:0 auto 14px}
.brand__name{font-family:"Oswald",sans-serif;font-weight:300;font-size:30px;color:var(--brown);letter-spacing:2px;line-height:1.05;text-transform:uppercase}
.welcome{left:81px;top:300px;font-size:28px;font-weight:300}
.cover-title{left:81px;top:345px;font-size:62px}
.social{left:90px;top:567px;display:flex;gap:10px}
.social span{width:33px;height:33px;border:1.5px solid var(--terracotta);border-radius:50%}

/* contacts */
.contacts{left:0;top:538px;width:100%}
.contact{position:absolute;display:flex;gap:20px;align-items:flex-start}
.contact__icon{width:54px;height:54px;border-radius:50%;background:var(--white);display:flex;align-items:center;justify-content:center;flex:none;margin-top:-6px}
.contact__text{color:var(--white);font-size:16px;line-height:26px}
</style>
</head>
<body>

<!-- Cover -->
<section class="slide slide--cover">
  <div class="abs brand">
    <div class="brand__mark"></div>
    <div class="brand__name">Casa<br>Orlena</div>
  </div>
  <div class="abs heading welcome">Welcome to</div>
  <div class="abs heading heading--plain cover-title">Casa Orlena</div>
  <div class="abs social"><span></span><span></span><span></span></div>

  <svg class="abs" style="left:0;top:0" width="1152" height="645" viewBox="0 0 1152 645">
    <defs>
      <linearGradient id="roomLiving" x1="0" y1="0" x2="0" y2="1">
        <stop offset="0" stop-color="#f6d8cc"/><stop offset=".62" stop-color="#f3cfc2"/><stop offset=".63" stop-color="#a87d5c"/><stop offset="1" stop-color="#8d6446"/>
      </linearGradient>
      <linearGradient id="roomChair" x1="0" y1="0" x2="0" y2="1">
        <stop offset="0" stop-color="#f0e6dc"/><stop offset=".75" stop-color="#ede2d6"/><stop offset=".76" stop-color="#c4925e"/>
      </linearGradient>
      <linearGradient id="roomLounge" x1="0" y1="0" x2="0" y2="1">
        <stop offset="0" stop-color="#e3e1df"/><stop offset=".6" stop-color="#e8b7b7"/><stop offset="1" stop-color="#7f7f8c"/>
      </linearGradient>
      <linearGradient id="roomBed" x1="0" y1="0" x2="0" y2="1">
        <stop offset="0" stop-color="#b08886"/><stop offset=".55" stop-color="#a27a78"/><stop offset=".7" stop-color="#8d1f2a"/><stop offset="1" stop-color="#1c1c1c"/>
      </linearGradient>
    </defs>
    <polygon points="225,0 525,0 355,165" fill="none" stroke="var(--pink-line)" stroke-width="2"/>
    <g role="img" aria-label="Illustration of a reading corner with a red armchair and floor lamp">
      <polygon points="240,0 560,0 390,170" fill="url(#roomChair)"/>
    </g>
    <polygon points="225,0 390,175 372,175 210,0" fill="var(--pink)"/>
    <polygon points="770,0 1152,0 1152,250 1075,250" fill="none" stroke="var(--pink-line)" stroke-width="2"/>
    <g role="img" aria-label="Illustration of a lounge with a pink sofa and patterned rug">
      <polygon points="790,0 1152,0 1152,185 1100,250" fill="url(#roomLounge)"/>
    </g>
    <polygon points="760,0 780,0 1100,255 1090,268" fill="var(--pink)"/>
    <polygon points="494,289 787,0 1080,289 787,582" fill="none" stroke="var(--pink-line)" stroke-width="2"/>
    <g role="img" aria-label="Illustration of a living room with a red sofa, sideboard and plants">
      <polygon points="520,289 787,22 1054,289 787,556" fill="url(#roomLiving)"/>
    </g>
    <polygon points="620,400 787,570 787,590 605,410" fill="var(--pink)"/>
    <polygon points="975,345 1152,320 1152,645 830,645" fill="none" stroke="var(--pink-line)" stroke-width="2"/>
    <polygon points="1140,320 1152,320 1152,645 830,645 860,615" fill="var(--pink)"/>
    <g role="img" aria-label="Illustration of a bedroom with a red bed and framed print">
      <polygon points="1152,345 1152,645 855,645"  fill="url(#roomBed)"/>
    </g>
  </svg>
</section>

<!-- Master bedroom -->
<section class="slide slide--bedroom">
  <div class="frame" style="left:540px;top:8px;width:620px;height:446px"></div>
  <div class="visual" role="img" aria-label="Render of the master bedroom with patterned wallpaper, chandelier and dark bed" style="left:548px;top:0;width:604px;height:446px;background:linear-gradient(180deg,#8c8c84 0%,#7b7d78 48%,#2c3037 52%,#353a42 80%,#a67444 82%,#8b5c33 100%)"></div>
  <div class="abs heading" style="left:29px;top:132px;font-size:48px">Master Bedroom</div>
  <p class="abs body-text" style="left:29px;top:216px;width:460px">Sed ut perspiciatis unde omnis iste natus error sit volup accusantium doloremque laudantium, totam rem aperiam, eaque ipsaquae ab illo inventore veritatis et quasi architecto beatae vitae dictunt explicabo. Nemo enim ipsam voluptatem quia voluptas sit aspernatur aut odit aut fugit, sed quia consequuntur magni dolores eos qui ratione.</p>
  <div class="frame" style="left:0;top:440px;width:548px;height:208px;border-width:2px 0 0 0"></div>
  <div class="block" style="left:339px;top:434px;width:209px;height:12px"></div>
  <div class="visual" role="img" aria-label="Side view of the bed with cushions and throw, wardrobe behind" style="left:0;top:446px;width:546px;height:202px;background:linear-gradient(180deg,#d8d6d0 0%,#3a3f48 30%,#40464f 65%,#9a6b3f 70%,#7a5330 100%)"></div>
  <div class="block" style="left:546px;top:446px;width:16px;height:202px"></div>
  <div class="abs" style="left:562px;top:451px;width:590px;height:197px;background:var(--white)"></div>
  <div class="abs subheading" style="left:603px;top:505px">The furnishings of the master bedroom</div>
  <p class="abs body-text" style="left:603px;top:552px;width:470px;font-size:12px">Sed ut perspiciatis unde omnis iste natus error sit volup accusantium doloremque laudantium, totam rem aperiam, eaque.</p>
</section>

<!-- Walk-in closet -->
<section class="slide slide--closet">
  <div class="abs" style="left:0;top:0;width:1152px;height:234px;background:var(--terracotta)"></div>
  <div class="abs heading" style="left:29px;top:100px;font-size:48px;color:var(--white)">Walk-in Closet</div>
  <div class="abs" style="left:29px;top:170px;font-size:20px;color:var(--white)">The furnishings of the walk-in closet</div>
  <p class="abs body-text" style="left:29px;top:270px;width:460px">Sed ut perspiciatis unde omnis iste natus error sit volup accusantium doloremque laudantium, totam rem aperiam, eaque ipsaquae ab illo inventore veritatis et quasi architecto beatae vitae dictunt explicabo. Nemo enim ipsam voluptatem quia voluptas sit aspernatur aut odit aut fugit, sed quia consequuntur magni dolores eos qui ratione.</p>
  <p class="abs body-text" style="left:29px;top:402px;width:460px">Sed ut perspiciatis unde omnis iste natus error sit volup accusantium doloremque laudantium, totam rem aperiam, eaque ipsaquae ab illo inventore veritatis et quasi architecto beatae vitae dictunt explicabo. Nemo enim ipsam voluptatem quia voluptas sit aspernatur aut odit aut fugit, sed quia consequuntur magni dolores eos qui ratione.</p>
  <div class="block" style="left:508px;top:84px;width:300px;height:210px"></div>
  <div class="frame" style="left:511px;top:94px;width:10px;height:554px;border-width:0 0 0 2px"></div>
  <div class="visual" role="img" aria-label="Render of open wardrobe with hanging clothes and drawers" style="left:517px;top:94px;width:291px;height:554px;background:linear-gradient(180deg,#f2f2f2 0%,#8a7a66 12%,#3b3a3a 22%,#e9e9e9 28%,#e4e4e4 36%,#2f2f30 42%,#7c6e55 60%,#242424 78%,#f3f3f3 86%,#8e6a44 100%)"></div>
  <div class="frame" style="left:851px;top:21px;width:290px;height:532px"></div>
  <div class="block" style="left:851px;top:540px;width:290px;height:13px"></div>
  <div class="block" style="left:1128px;top:21px;width:13px;height:532px"></div>
  <div class="visual" role="img" aria-label="Render of closet with shoe shelves, ladder and hanging coats" style="left:833px;top:0;width:289px;height:532px;background:linear-gradient(90deg,#dedede 0%,#3a3634 22%,#6d5f55 40%,#4a4b55 60%,#8b7356 78%,#c8c8c8 100%)"></div>
</section>

<!-- Master bathroom -->
<section class="slide slide--bathroom">
  <div class="abs" style="left:1052px;top:0;width:100px;height:648px;background:var(--terracotta)"></div>
  <div class="block" style="left:28px;top:256px;width:12px;height:296px"></div>
  <div class="block" style="left:28px;top:540px;width:381px;height:12px"></div>
  <div class="frame" style="left:52px;top:100px;width:381px;height:438px"></div>
  <div class="visual" role="img" aria-label="Render of master bathroom with freestanding tub, window and patterned floor" style="left:40px;top:113px;width:380px;height:427px;background:linear-gradient(180deg,#2c2f36 0%,#31343b 40%,#b4b4b4 42%,#c6c6c6 70%,#e9e9e9 78%,#3f4548 88%,#d7d7cc 100%)"></div>
  <div class="abs heading" style="left:495px;top:122px;font-size:48px">Master Bathroom</div>
  <p class="abs body-text" style="left:491px;top:200px;width:460px">Sed ut perspiciatis unde omnis iste natus error sit volup accusantium doloremque laudantium, totam rem aperiam, eaque ipsaquae ab illo inventore veritatis et quasi architecto beatae vitae dictunt explicabo. Nemo enim ipsam voluptatem quia voluptas sit aspernatur aut odit aut fugit, sed quia consequuntur magni dolores eos qui ratione.</p>
  <div class="abs subheading" style="left:491px;top:351px">The furniture of the master bathroom</div>
  <p class="abs body-text" style="left:491px;top:404px;width:460px">Sed ut perspiciatis unde omnis iste natus error sit volup accusantium doloremque laudantium, totam rem aperiam, eaque ipsaquae ab illo inventore veritatis et quasi architecto beatae vitae dictunt explicabo. Nemo enim ipsam voluptatem quia voluptas sit aspernatur aut odit aut fugit, sed quia consequuntur magni dolores eos qui ratione.</p>
</section>

<!-- Thank you -->
<section class="slide slide--thanks">
  <div class="abs" style="left:0;top:297px;width:1152px;height:351px;background:var(--terracotta)"></div>
  <div class="abs heading heading--plain" style="left:0;top:88px;width:1152px;justify-content:center;font-size:48px">Thank you</div>
  <div class="frame" style="left:796px;top:174px;width:72px;height:70px"></div>
  <div class="block" style="left:284px;top:242px;width:12px;height:230px"></div>
  <div class="block" style="left:284px;top:460px;width:258px;height:12px"></div>
  <div class="visual" role="img" aria-label="Illustration of a living room with yellow sofa, shelves, lamp and TV unit" style="left:296px;top:183px;width:562px;height:280px;background:linear-gradient(180deg,#f5d7a6 0%,#f1cf9a 62%,#e8a23a 64%,#e49a30 78%,#c8623a 82%,#b85a36 100%)"></div>
  <div class="abs contacts">
    <div class="contact" style="left:171px">
      <div class="contact__icon">
        <svg width="22" height="26" viewBox="0 0 22 26"><path d="M11 1C5.5 1 1.5 5 1.5 10.2 1.5 17 11 25 11 25s9.5-8 9.5-14.8C20.5 5 16.5 1 11 1z" fill="var(--pink)"/><circle cx="11" cy="10" r="3.4" fill="#fff"/></svg>
      </div>
      <div class="contact__text">ADDRESS:<br>di Marta Vellani<br>via dei Tigli, 24</div>
    </div>
    <div class="contact" style="left:488px">
      <div class="contact__icon">
        <svg width="24" height="24" viewBox="0 0 24 24"><path d="M6.6 2.5 9.5 7c.4.6.3 1.4-.2 1.9L7.7 10.5c1.4 2.8 3.1 4.5 5.8 5.8l1.6-1.6c.5-.5 1.3-.6 1.9-.2l4.5 2.9c.6.4.8 1.2.4 1.8l-1.4 2.3c-.6 1-1.8 1.4-2.9 1.1C10.4 20.9 3.1 13.6 1.4 6.4 1.1 5.3 1.5 4.1 2.5 3.5l2.3-1.4c.6-.4 1.4-.2 1.8.4z" fill="var(--pink)"/></svg>
      </div>
      <div class="contact__text">PHONE:<br>345/1182036</div>
    </div>
    <div class="contact" style="left:742px">
      <div class="contact__icon">
        <svg width="26" height="20" viewBox="0 0 26 20"><rect x="1" y="1" width="24" height="18" rx="2" fill="var(--pink)"/><path d="M2 3l11 8 11-8" fill="none" stroke="#fff" stroke-width="2"/></svg>
      </div>
      <div class="contact__text">EMAIL:<br>marta.vellani@studiomail.com</div>
    </div>
  </div>
</section>

</body>
</html>
```